SaaS Early tech startup business card design

Unique design for experience ecommerce platform company. the business cards will be used by executive members. conformance with color code is required.

```html
<!DOCTYPE html>
<html lang="en">
<head>
<meta charset="utf-8">
<title>Kelto Business Card</title>
<link rel="stylesheet" href="https://fonts.googleapis.com/css2?family=Arimo:wght@400;700&display=swap">
<style>
  :root {
    --teal: #1eb39b;
    --blue: #17739e;
    --ink: #4a4a4a;
    --rule: #6b6b6b;
    --card: #ffffff;
    --stage: #e6e8ea;
  }
  * { margin: 0; padding: 0; box-sizing: border-box; }
  html, body {
    width: 1200px; height: 900px; overflow: hidden;
    background: var(--stage);
    font-family: "Arimo", Arial, sans-serif;
  }
  .canvas { position: relative; width: 1200px; height: 900px; }
  .card {
    position: absolute;
    width: 525px; height: 300px;
    background: var(--card);
    border-radius: 22px;
    box-shadow: 0 6px 18px rgba(0,0,0,0.15);
    overflow: hidden;
  }
  .card-front { left: 90px; top: 110px; }
  .card-back { left: 585px; top: 490px; }

  .wordmark {
    font-weight: 700;
    color: var(--teal);
    letter-spacing: 1px;
    line-height: 1;
  }
  .card-front .wordmark {
    position: absolute; left: 0; right: 0; top: 108px;
    text-align: center; font-size: 84px;
  }
  .card-back .wordmark {
    position: absolute; right: 40px; top: 30px;
    font-size: 64px;
  }

  .holder {
    position: absolute; left: 34px; top: 134px;
    line-height: 1.15;
  }
  .holder-name { font-size: 24px; font-weight: 700; color: var(--teal); }
  .holder-role { font-size: 17px; color: var(--ink); margin-top: 2px; }

  .address {
    position: absolute; right: 34px; top: 136px;
    text-align: right; font-size: 15px; color: var(--ink); line-height: 1.35;
  }

  .divider {
    position: absolute; left: 34px; right: 34px; top: 198px;
    height: 1px; background: var(--rule);
  }

  .contacts {
    position: absolute; left: 34px; top: 208px;
    list-style: none;
  }
  .contact {
    display: flex; align-items: center; gap: 10px;
    font-size: 17px; color: var(--ink); height: 26px;
  }
  .contact-icon { width: 20px; height: 20px; flex: none; }
</style>
</head>
<body>
<main class="canvas">

  <section class="card card-front" aria-label="Card front">
    <div class="wordmark">kelto</div>
  </section>

  <section class="card card-back" aria-label="Card back">
    <div class="wordmark">kelto</div>

    <div class="holder">
      <div class="holder-name">Daniel Hart</div>
      <div class="holder-role">Manager</div>
    </div>

    <div class="address">Your address, city<br>state, ZIP 0000</div>

    <div class="divider"></div>

    <ul class="contacts">
      <li class="contact">
        <svg class="contact-icon" viewBox="0 0 20 20" aria-hidden="true">
          <rect width="20" height="20" rx="4" fill="var(--teal)"/>
          <path d="M6 4.5l2 .3.8 2.7-1.3 1a7 7 0 0 0 3.9 3.9l1-1.3 2.7.8.3 2c-.2.9-1 1.3-1.8 1.3A10 10 0 0 1 4.6 6.3c0-.8.5-1.6 1.4-1.8z" fill="#fff"/>
        </svg>
        555-014-2730
      </li>
      <li class="contact">
        <svg class="contact-icon" viewBox="0 0 20 20" aria-hidden="true">
          <rect width="20" height="20" rx="4" fill="var(--teal)"/>
          <rect x="4" y="6" width="12" height="8.5" fill="none" stroke="#fff" stroke-width="1.4"/>
          <path d="M4 6l6 5 6-5M4 14.5l4.5-4M16 14.5l-4.5-4" fill="none" stroke="#fff" stroke-width="1.2"/>
        </svg>
        youremail@keltomail.com
      </li>
      <li class="contact">
        <svg class="contact-icon" viewBox="0 0 20 20" aria-hidden="true">
          <rect width="20" height="20" rx="4" fill="var(--teal)"/>
          <circle cx="10" cy="10" r="5.8" fill="none" stroke="#fff" stroke-width="1.4"/>
          <ellipse cx="10" cy="10" rx="2.5" ry="5.8" fill="none" stroke="#fff" stroke-width="1.1"/>
          <path d="M4.2 10h11.6" stroke="#fff" stroke-width="1.1"/>
        </svg>
        www.keltoapp.com
      </li>
    </ul>
  </section>

</main>
</body>
</html>
```